Law Firm in Texas in need of new letterhead

Law Firm in Fort Worth, TX, USA named "Pell & Varnum, Attorneys-At-Law, LLP." This is a general practice law firm that mostly does Family Law and Criminal Defense work.

We are looking for a new letterhead that has a "classical" appeal, with modern elements.

Any color combination is fine, but please note that we do fax many documents, so the design must be clearly legible in Black and White.

We would like our letterhead to project a sense of professionalism, integrity, and ability.

Target Market(s)

Letterhead will be for correspondence generally with other attorneys and clients.

Industry/Entity Type

Law Firm

Logo Text

Pell & Varnum, Attorneys-At-Law, LLP.

Logo styles of interest
Pictorial/Combination Logo
Wordmark Logo
Lettermark Logo
Requirements
Nice to have
• Although not necessary, a "Texas Star" that is incorporated into the design would be a nice touch.
Should not have
• Colors that do not convert to B&W easily

```html
<!DOCTYPE html>
<html lang="en">
<head>
<meta charset="utf-8">
<title>Pell &amp; Varnum Letterhead</title>
<link href="https://fonts.googleapis.com/css2?family=Cinzel:wght@500;600&family=Montserrat:wght@400;600&display=swap" rel="stylesheet">
<style>
  :root {
    --backdrop: #d9d9db;
    --paper: #ffffff;
    --brand-blue: #2f5d8f;
    --ink: #4a4a4a;
    --muted: #8a8a8a;
    --rule: #2f5d8f;
  }
  * { box-sizing: border-box; margin: 0; padding: 0; }
  html, body {
    width: 1200px; height: 1000px; overflow: hidden;
    background: var(--backdrop);
  }
  .canvas {
    width: 1200px; height: 1000px;
    display: flex; align-items: center; justify-content: center;
  }
  .letterhead {
    position: relative;
    width: 700px; height: 920px;
    background: var(--paper);
    box-shadow: 0 4px 18px rgba(0,0,0,0.12);
    padding: 56px 70px 0;
    font-family: "Montserrat", sans-serif;
    color: var(--ink);
  }
  .firm-name {
    text-align: center;
    font-family: "Cinzel", serif;
    font-weight: 600;
    color: var(--brand-blue);
    font-size: 30px;
    letter-spacing: 1px;
    line-height: 1;
  }
  .firm-tagline {
    display: flex; align-items: center; justify-content: center; gap: 10px;
    margin-top: 6px;
    font-family: "Cinzel", serif;
    font-weight: 500;
    color: var(--brand-blue);
    font-size: 15px;
    letter-spacing: 1px;
  }
  .firm-tagline .rule {
    width: 46px; height: 1px; background: var(--brand-blue);
  }
  .letter-body {
    margin-top: 110px;
    font-size: 12px;
    line-height: 1.55;
    text-align: justify;
  }
  .letter-body p { margin-bottom: 14px; }
  .sign-off {
    margin-top: 6px;
    text-align: right;
    font-size: 12px;
  }
  .signature-row {
    display: flex; justify-content: flex-end; align-items: center; gap: 18px;
    margin-top: 10px;
  }
  .signature-mark {
    width: 130px; height: 46px;
    background: linear-gradient(90deg, #e7edf6, #d3def0);
    border-radius: 4px;
  }
  .signer-name {
    font-weight: 600; font-size: 13px; color: #222;
  }
  .footer {
    position: absolute; left: 36px; right: 36px; bottom: 48px;
    display: grid;
    grid-template-columns: 132px 132px 200px 164px;
    font-size: 9.5px;
    line-height: 1.5;
    color: var(--muted);
    align-items: end;
  }
  .footer-block {
    border-left: 1px solid var(--rule);
    padding: 4px 10px 6px;
    white-space: nowrap;
    height: 72px;
    display: flex; flex-direction: column; justify-content: flex-end;
  }
  .footer-block .label { color: var(--brand-blue); font-weight: 600; }
  .footer-block .value { color: var(--brand-blue); }
  .footer-block .attorney { color: #555; font-weight: 600; text-transform: uppercase; }
  .footer-block:nth-child(1) { padding-bottom: 6px; }
  .footer-block:nth-child(2) { padding-bottom: 20px; }
  .footer-block:nth-child(3) { padding-bottom: 10px; }
  .footer-block:nth-child(4) { padding-bottom: 40px; }
</style>
</head>
<body>
<div class="canvas">
  <article class="letterhead">
    <header class="masthead">
      <h1 class="firm-name">Pell &amp; Varnum</h1>
      <div class="firm-tagline"><span class="rule"></span><span>Attorneys At Law, LLP</span><span class="rule"></span></div>
    </header>

    <section class="letter-body">
      <p>Lorem ipsum dolor sit amet, consectetur adipisicing elit, sed do eiusmod tempor incididunt ut labore et dolore magna aliqua. Ut enim ad minim veniam, quis nostrud exercitation ullamco laboris nisi ut aliquip ex ea commodo consequat. Duis aute irure dolor in reprehenderit in voluptate velit esse cillum dolore eu fugiat nulla pariatur. Excepteur sint occaecat cupidatat non proident, sunt in culpa qui officia deserunt mollit anim id est laborum.</p>
      <p>Sed do eiusmod tempor incididunt ut labore et dolore magna aliqua. Ut enim ad minim veniam, quis nostrud exercitation ullamco laboris nisi ut aliquip ex ea commodo consequat. Duis aute irure dolor in reprehenderit in voluptate velit esse cillum dolore eu fugiat nulla pariatur. Excepteur sint occaecat cupidatat non proident, sunt in culpa qui officia deserunt mollit anim id est laborum.</p>
      <p>Lorem ipsum dolor sit amet, consectetur adipisicing elit, sed do eiusmod tempor incididunt ut labore et dolore magna aliqua. Ut enim ad minim veniam, quis nostrud exercitation ullamco laboris nisi ut aliquip ex ea commodo consequat. Duis aute irure dolor in reprehenderit in voluptate velit esse cillum dolore eu fugiat nulla pariatur.</p>
      <p>Lorem ipsum dolor sit amet, consectetur adipisicing elit, sed do eiusmod tempor incididunt ut labore et dolore magna aliqua. Ut enim ad minim veniam, quis nostrud exercitation ullamco laboris nisi ut aliquip ex ea commodo consequat. Duis aute irure dolor in reprehenderit in voluptate velit esse cillum dolore eu fugiat nulla pariatur. Excepteur sint occaecat cupidatat non proident, sunt in culpa qui officia deserunt mollit anim id est laborum.</p>
    </section>

    <div class="sign-off">Yours Sincerely,</div>
    <div class="signature-row">
      <div class="signature-mark" role="img" aria-label="Handwritten signature in blue ink"></div>
      <div class="signer-name">Dana Whitlow</div>
    </div>

    <footer class="footer">
      <div class="footer-block"><span>1820 W. Magnolia Ave.</span><span>Fort Worth, TX 76104</span></div>
      <div class="footer-block"><span><span class="label">Phone:</span> <span class="value">(817) 555-0142</span></span><span><span class="label">Fax:</span> <span class="value">(817) 555-0187</span></span></div>
      <div class="footer-block"><span><span class="attorney">Nathan Pell</span> - Managing Partner</span><span>- Licensed in State of Texas</span><span>- United States District Court</span><span>- United States Supreme Court</span></div>
      <div class="footer-block"><span class="attorney">Lydia Marie Varnum</span><span>- Licensed in the State of Texas</span></div>
    </footer>
  </article>
</div>
</body>
</html>
```